Ward Compass Business Card Design*

We need a business card design for our company Ward Compass. Our company is specialized in providing online consulting services regarding medical institutions, hospitals and doctors. We work with patients worldwide looking to choose between healthcare providers. We have a website you may use as a reference, where we list doctors and clinics worldwide. So we target Medical providers as well as patients worldwide.
Target Market(s)
Medical Providers and patients around the world
Industry/Entity Type
Medical
Contact Information for Business Card
Salwa Kettani
CEO
+90 612 348 2175
info@wardcompass.example
www.wardcompass.example
14 Annakhil 7 H.R.B. Rabat, Morocco
Requirements
Must have
- Company logo/name on one full side, personal info and smaller logo and company name on the other side.
Nice to have
- Smart and elegant design

```html
<!DOCTYPE html>
<html lang="en">
<head>
<meta charset="utf-8">
<title>Ward Compass Business Card</title>
<link rel="stylesheet" href="https://fonts.googleapis.com/css2?family=Roboto:wght@400;500;700&display=swap">
<style>
  :root {
    --navy: #15386a;
    --white: #ffffff;
    --grey: #7a7a7a;
    --backdrop: #e9ebef;
  }
  * { box-sizing: border-box; margin: 0; padding: 0; }
  html, body {
    width: 1200px; height: 1000px; overflow: hidden;
    background: var(--backdrop);
    font-family: "Roboto", Arial, sans-serif;
  }
  .sheet {
    width: 1200px; height: 1000px;
    display: flex; flex-direction: column; align-items: center; justify-content: center;
    gap: 44px;
  }
  .card {
    position: relative;
    width: 760px; height: 434px;
    border-radius: 26px;
    background: var(--navy);
    overflow: hidden;
    box-shadow: 0 10px 30px rgba(20, 30, 50, 0.18);
  }
  /* Front */
  .card-front { display: flex; align-items: center; justify-content: center; }
  .brand { display: flex; align-items: center; gap: 22px; }
  .brand-dot { width: 62px; height: 62px; border-radius: 50%; background: var(--grey); }
  .brand-name {
    font-weight: 500; font-size: 44px; letter-spacing: 3px;
    text-transform: uppercase; color: var(--white);
  }
  /* Back */
  .back-circle {
    position: absolute; left: 402px; top: 98px;
    width: 640px; height: 640px; border-radius: 50%;
    background: var(--white);
  }
  .back-brand {
    position: absolute; left: 448px; top: 246px;
    font-weight: 500; font-size: 31px; letter-spacing: 2px;
    text-transform: uppercase; color: var(--navy);
  }
  .person { position: absolute; left: 64px; top: 70px; color: var(--white); }
  .person-name { font-weight: 500; font-size: 24px; letter-spacing: 1px; text-transform: uppercase; }
  .person-role { font-weight: 500; font-size: 20px; margin-top: 6px; }
  .divider { width: 30px; height: 4px; background: var(--white); margin-top: 22px; }
  .contact { position: absolute; left: 64px; top: 212px; color: var(--white); font-size: 17px; line-height: 1.3; }
  .address { margin-bottom: 14px; }
  .contact-list { list-style: none; }
  .contact-list li { display: flex; align-items: center; gap: 10px; margin-bottom: 9px; }
  .contact-list svg { width: 15px; height: 15px; flex: none; }
</style>
</head>
<body>
<main class="sheet">
  <section class="card card-front" aria-label="Card front">
    <div class="brand">
      <span class="brand-dot"></span>
      <span class="brand-name">Ward Compass</span>
    </div>
  </section>

  <section class="card card-back" aria-label="Card back">
    <div class="back-circle"></div>
    <div class="back-brand">Ward Compass</div>

    <div class="person">
      <div class="person-name">Salwa Kettani</div>
      <div class="person-role">CEO</div>
      <div class="divider"></div>
    </div>

    <div class="contact">
      <p class="address">14 Annakhil 7 H.R.B.<br>Rabat, Morocco</p>
      <ul class="contact-list">
        <li>
          <svg viewBox="0 0 16 16" aria-hidden="true"><path d="M3.5 1.5l2.5 0.5 1 3-1.8 1.3a8 8 0 0 0 4.5 4.5L11 9l3 1 0.5 2.5-2 2C7 14 2 9 1.5 3.5z" fill="none" stroke="#fff" stroke-width="1.4" stroke-linejoin="round"/></svg>
          <span>+90 612 348 2175</span>
        </li>
        <li>
          <svg viewBox="0 0 16 16" aria-hidden="true"><rect x="1" y="3" width="14" height="10" rx="1" fill="none" stroke="#fff" stroke-width="1.4"/><path d="M1.5 3.5L8 9l6.5-5.5" fill="none" stroke="#fff" stroke-width="1.4"/></svg>
          <span>info@wardcompass.example</span>
        </li>
        <li>
          <svg viewBox="0 0 16 16" aria-hidden="true"><circle cx="8" cy="8" r="6.5" fill="none" stroke="#fff" stroke-width="1.4"/><path d="M1.5 8h13M8 1.5c-3 3.5-3 9.5 0 13M8 1.5c3 3.5 3 9.5 0 13" fill="none" stroke="#fff" stroke-width="1.1"/></svg>
          <span>www.wardcompass.example</span>
        </li>
      </ul>
    </div>
  </section>
</main>
</body>
</html>
```